Black Matte card with samurai logo which I would like it to be textured and company name on one side and on the other side I would like the company information with the reno (Face logo) Sushi logo. Double Sided card.

majority customers are University students, University sororities and fraternities.

It Company

Reno Sushi
317 W. Harlow Ave
Tucson, AZ 85042
Phone (520)413-6271
Fax (520)357-1846
E-mail: Renosushidesert@mailbox-example.com
FB: Renosushidesert
Twitter: Renosushidesert

• Present Normal

```html
<!DOCTYPE html>
<html lang="en">
<head>
<meta charset="utf-8">
<title>Reno Sushi – Business Card</title>
<link rel="stylesheet" href="https://fonts.googleapis.com/css2?family=Source+Sans+3:wght@400;600&display=swap">
<style>
  :root {
    --backdrop: #e6e4e1;
    --card-black: #0d0d0d;
    --card-white: #ffffff;
    --card-edge: #3a3a3a;
    --sushi-red: #b0231f;
    --ink: #3d3d3d;
    --paper-text: #ffffff;
    --social-blue: #4a6aa8;
    --social-sky: #4fb3dd;
  }
  * { box-sizing: border-box; margin: 0; padding: 0; }
  html, body {
    width: 1200px;
    height: 1115px;
    overflow: hidden;
    background: var(--backdrop);
    font-family: "Source Sans 3", "Myriad Pro", sans-serif;
  }
  .canvas { position: relative; width: 1200px; height: 1115px; }

  .card { position: absolute; width: 846px; height: 484px; overflow: hidden; }

  /* Front: black matte, crumpled texture */
  .card--front {
    left: 48px; top: 36px;
    background: var(--card-black);
  }
  .matte-texture {
    position: absolute; inset: 0;
    width: 100%; height: 100%;
  }
  .front-mark {
    position: absolute;
    left: 363px; top: 80px;
    width: 120px; height: 120px;
    border-radius: 50%;
    background: var(--sushi-red);
  }
  .front-name {
    position: absolute;
    left: 0; right: 0; top: 372px;
    text-align: center;
    font-size: 84px; font-weight: 400;
    color: var(--paper-text);
    letter-spacing: 1px; line-height: 1;
  }

  /* Back: contact details */
  .card--back {
    left: 295px; top: 572px;
    height: 483px;
    background: var(--card-white);
    border: 1.5px solid var(--card-edge);
  }
  .back-mark {
    position: absolute;
    left: 104px; top: 30px;
    width: 92px; height: 92px;
    border-radius: 50%;
    background: var(--sushi-red);
  }
  .back-name {
    position: absolute;
    left: 40px; width: 220px; top: 150px;
    text-align: center;
    font-size: 50px; font-weight: 400;
    color: var(--sushi-red); line-height: 1;
  }

  .contact-list {
    position: absolute; left: 46px; top: 302px;
    list-style: none; font-size: 21px; color: var(--ink);
  }
  .contact-list li { display: flex; align-items: center; gap: 10px; height: 32px; }
  .contact-list svg { width: 18px; height: 18px; flex: none; fill: var(--sushi-red); }

  .address {
    position: absolute; left: 46px; top: 417px;
    font-size: 21px; color: var(--ink);
  }

  .social-list {
    position: absolute; left: 590px; top: 330px;
    list-style: none; font-size: 21px; color: var(--ink);
  }
  .social-list li { display: flex; align-items: center; gap: 10px; height: 31px; }
  .social-mark { width: 19px; height: 19px; border-radius: 2px; flex: none; }
  .social-mark--a { background: var(--social-blue); }
  .social-mark--b { background: var(--social-sky); }
</style>
</head>
<body>
<main class="canvas">

  <section class="card card--front" aria-label="Card front">
    <svg class="matte-texture" viewBox="0 0 846 484" preserveAspectRatio="none" aria-hidden="true">
      <defs>
        <filter id="crumple" x="0" y="0" width="100%" height="100%">
          <feTurbulence type="fractalNoise" baseFrequency="0.011 0.016" numOctaves="4" seed="7" result="noise"/>
          <feDiffuseLighting in="noise" lighting-color="#6a6a6a" surfaceScale="7">
            <feDistantLight azimuth="225" elevation="38"/>
          </feDiffuseLighting>
        </filter>
        <radialGradient id="vignette" cx="45%" cy="45%" r="70%">
          <stop offset="0" stop-color="#000" stop-opacity="0"/>
          <stop offset="1" stop-color="#000" stop-opacity="0.75"/>
        </radialGradient>
      </defs>
      <rect width="846" height="484" filter="url(#crumple)" opacity="0.5"/>
      <rect width="846" height="484" fill="url(#vignette)"/>
    </svg>
    <span class="front-mark" aria-hidden="true"></span>
    <p class="front-name">reno sushi</p>
  </section>

  <section class="card card--back" aria-label="Card back">
    <span class="back-mark" aria-hidden="true"></span>
    <p class="back-name">reno sushi</p>

    <ul class="contact-list">
      <li>
        <svg viewBox="0 0 24 24" aria-hidden="true"><path d="M6.6 10.8a15.1 15.1 0 0 0 6.6 6.6l2.2-2.2a1 1 0 0 1 1-.25 11.4 11.4 0 0 0 3.6.6 1 1 0 0 1 1 1V20a1 1 0 0 1-1 1A17 17 0 0 1 3 4a1 1 0 0 1 1-1h3.5a1 1 0 0 1 1 1c0 1.25.2 2.45.6 3.6a1 1 0 0 1-.25 1z"/></svg>
        <span>(520)413-6271</span>
      </li>
      <li>
        <svg viewBox="0 0 24 24" aria-hidden="true"><path d="M7 2h10a1.5 1.5 0 0 1 1.5 1.5v17A1.5 1.5 0 0 1 17 22H7a1.5 1.5 0 0 1-1.5-1.5v-17A1.5 1.5 0 0 1 7 2zm1 3v9h8V5zm1 11v2h2v-2zm4 0v2h2v-2z"/></svg>
        <span>(520)357-1846</span>
      </li>
      <li>
        <svg viewBox="0 0 24 24" aria-hidden="true"><path d="M2 8l10-5 10 5v12H2zm2 1.2V18h16V9.2l-8 5z"/></svg>
        <span>Renosushidesert@mailbox-example.com</span>
      </li>
    </ul>

    <p class="address">Reno Sushi 317 W. Harlow Ave Tucson, AZ 85042</p>

    <ul class="social-list">
      <li><span class="social-mark social-mark--a"></span><span>Renosushidesert</span></li>
      <li><span class="social-mark social-mark--b"></span><span>Renosushidesert</span></li>
    </ul>
  </section>

</main>
</body>
</html>
```